Business Cards Design for the electrical wholesaler: clean bold dynamic :)

We need a business card design that would follow our latest brand guidelines. As an electrical wholesaler we want to bring a fresh look and feel into the industry. The design should be clean bold and dynamic. It should come alive with the renewed energy of our green colour. Our grey colour should keep things balanced and complement the notion of maturity and responsibility. We employ Lato as a corporate font however are not bound by this font and we’re open to interpretation here.

Target Market(s)

Electrical contractors

Industry/Entity Type

Business

Contact Information for Business Card

Logo
Name & Surname: Halyna Dorosh
Job Title: Director of Marketing
Email: halya.dorosh@quillmail.example
Cell phone: XXX.XXX.XXXX
Address: 20517 - 87 Ave. Edmonton, AB, Canada. T6K 4N8
Business Phone: 780.555.0184
Website: www.brovix.example

Font styles to use
Other font styles liked:
• Lato

Requirements
Must have
• Logo & website
Nice to have
• Brand elements - some of them you may find in the attached Brand Guidelines (e.g. three lines on the background signifying "W")

```html
<!DOCTYPE html>
<html lang="en">
<head>
<meta charset="utf-8">
<title>Brovix Business Card</title>
<link href="https://fonts.googleapis.com/css2?family=Lato:wght@400;700&family=Play:wght@700&display=swap" rel="stylesheet">
<style>
  :root {
    --backdrop: #3a3a3b;
    --card: #1c1c1d;
    --card-back: #262627;
    --green: #7dc122;
    --white: #f2f2f2;
    --grey: #9a9a9a;
    --logo-gloss: #0c0c0c;
  }
  * { margin: 0; padding: 0; box-sizing: border-box; }
  html, body {
    width: 799px; height: 1200px; overflow: hidden;
    background: var(--backdrop);
    font-family: "Lato", sans-serif;
  }
  .sheet {
    position: relative; width: 799px; height: 1200px;
    display: flex; flex-direction: column; align-items: center;
    justify-content: space-around; padding: 60px 0;
  }
  .card {
    position: relative; width: 640px; height: 366px;
    border-radius: 26px; overflow: hidden;
    box-shadow: 0 14px 30px rgba(0,0,0,.45);
  }
  .card-front { background: var(--card); }
  .front-brand {
    position: absolute; left: 0; right: 0; top: 50%;
    transform: translateY(-50%);
    display: flex; align-items: center; justify-content: center; gap: 18px;
  }
  .front-brand .mark-dot {
    width: 58px; height: 58px; border-radius: 50%; background: var(--logo-gloss);
  }
  .front-brand .brand-name {
    font-family: "Lato", sans-serif; font-weight: 700; font-size: 92px;
    color: var(--logo-gloss); letter-spacing: 1px;
  }
  .card-back { background: var(--card-back); }
  .green-panel { position: absolute; right: 0; top: 0; width: 300px; height: 366px; }
  .back-brand {
    position: absolute; left: 32px; top: 30px;
    display: flex; align-items: center; gap: 10px;
  }
  .back-brand .mark-dot { width: 30px; height: 30px; border-radius: 50%; background: var(--green); }
  .back-brand .brand-name { font-weight: 700; font-size: 40px; color: var(--white); }
  .contact { position: absolute; left: 32px; top: 118px; color: var(--white); }
  .contact .person-name {
    font-family: "Play", sans-serif; font-weight: 700; font-size: 30px; color: var(--green);
  }
  .contact .job-title { font-size: 17px; margin-top: 2px; }
  .contact .address { font-size: 15px; line-height: 1.35; margin-top: 16px; }
  .contact .lines { margin-top: 14px; font-size: 15px; }
  .contact .line { display: flex; align-items: center; gap: 9px; margin-top: 6px; }
  .icon { width: 16px; height: 16px; flex: none; }
</style>
</head>
<body>
<main class="sheet">
  <section class="card card-front" aria-label="Card front">
    <div class="front-brand">
      <span class="mark-dot"></span>
      <span class="brand-name">Brovix</span>
    </div>
  </section>

  <section class="card card-back" aria-label="Card back">
    <svg class="green-panel" viewBox="0 0 300 366" aria-hidden="true">
      <path d="M30 0 H300 V366 H60 Q30 366 30 330 Z" fill="var(--green)"/>
      <path d="M150 0 H190 V366 H150 Z" fill="var(--card-back)"/>
    </svg>
    <div class="back-brand">
      <span class="mark-dot"></span>
      <span class="brand-name">Brovix</span>
    </div>
    <div class="contact">
      <div class="person-name">Halyna Dorosh</div>
      <div class="job-title">Founder &amp; CEO</div>
      <div class="address">20517 - 87 Ave. Edmonton,<br>AB, Canada T6K 4N8</div>
      <div class="lines">
        <div class="line">
          <svg class="icon" viewBox="0 0 16 16" aria-hidden="true"><circle cx="8" cy="8" r="8" fill="var(--green)"/><path d="M5 4.5l2 .5.3 2-1 .8a5 5 0 0 0 2 2l.8-1 2 .3.4 2c-3 1-7-3-6.5-6.6z" fill="var(--card-back)"/></svg>
          <span>+1 780-555-0184</span>
        </div>
        <div class="line">
          <svg class="icon" viewBox="0 0 16 16" aria-hidden="true"><circle cx="8" cy="8" r="8" fill="var(--green)"/><rect x="4" y="5.5" width="8" height="5.5" fill="var(--card-back)"/><path d="M4 5.5l4 3 4-3" stroke="var(--green)" fill="none"/></svg>
          <span>halya.dorosh@quillmail.example</span>
        </div>
        <div class="line">
          <svg class="icon" viewBox="0 0 16 16" aria-hidden="true"><circle cx="8" cy="8" r="8" fill="var(--green)"/><circle cx="8" cy="8" r="4.5" fill="none" stroke="var(--card-back)" stroke-width="1.3"/><path d="M3.5 8h9M8 3.5v9" stroke="var(--card-back)" stroke-width="1.1"/></svg>
          <span>www.brovix.example</span>
        </div>
      </div>
    </div>
  </section>
</main>
</body>
</html>
```